Business Cards - Brightpath Horizon

need to design unique business card for my mortgage business. I need to design credit card style business card for my business or any unique idea that you might have

Target Market(s)

Home Loan customers

Industry/Entity Type

Mortgage Brokerage

Contact Information for Business Card

please design credit card style or very unique style business card

Colors

Designer to choose colors to be used in the design.

Requirements
Must have
• Name
• position
• Phone number
• fax number
• email address
• website address
• social media address
• All above fields will be provided once design in finalised

```html
<!DOCTYPE html>
<html lang="en">
<head>
<meta charset="utf-8">
<title>Brightpath Horizon – Business Card</title>
<link rel="stylesheet" href="https://fonts.googleapis.com/css2?family=Oswald:wght@500&family=Arimo:wght@400&display=swap">
<style>
  :root {
    --backdrop: #d9d9d9;
    --orange: #f48a20;
    --orange-deep: #e97f1a;
    --white: #ffffff;
    --name-blue: #2aa5df;
    --ink: #4a4a4a;
    --muted: #6b6b6b;
    --divider: #f48a20;
  }
  * { box-sizing: border-box; margin: 0; padding: 0; }
  html, body { width: 1200px; height: 800px; overflow: hidden; }
  body {
    background: var(--backdrop);
    display: flex;
    align-items: center;
    justify-content: center;
    gap: 40px;
  }
  .card {
    position: relative;
    width: 525px;
    height: 300px;
    overflow: hidden;
    box-shadow: 0 3px 10px rgba(0,0,0,0.18);
  }

  /* Front */
  .card--front { background: var(--orange); color: var(--white); }
  .card__tree-decor {
    position: absolute;
    left: 250px; top: 20px;
    width: 230px; height: 230px;
    border-radius: 50% 50% 44% 44%;
    background: radial-gradient(circle at 50% 40%, var(--orange-deep), rgba(233,127,26,0) 72%);
  }
  .brand {
    position: absolute;
    left: 0; right: 0; top: 120px;
    display: flex;
    align-items: center;
    justify-content: center;
    gap: 12px;
  }
  .brand__mark {
    width: 16px; height: 16px;
    border-radius: 50%;
    background: var(--white);
    flex: none;
  }
  .brand__name {
    font-family: "Arimo", sans-serif;
    font-size: 32px;
    font-weight: 400;
    line-height: 1;
    color: var(--white);
  }
  .card__website {
    position: absolute;
    left: 0; right: 0; bottom: 34px;
    text-align: center;
    font-family: "Arimo", sans-serif;
    font-size: 12px;
    letter-spacing: 1.5px;
  }

  /* Back */
  .card--back { background: var(--white); }
  .identity {
    position: absolute;
    right: 300px; top: 118px;
    text-align: right;
  }
  .identity__name {
    font-family: "Oswald", sans-serif;
    font-weight: 500;
    font-size: 25px;
    color: var(--name-blue);
    text-transform: uppercase;
    letter-spacing: 0.5px;
    line-height: 1;
  }
  .identity__role {
    margin-top: 3px;
    font-family: "Arimo", sans-serif;
    font-size: 12px;
    color: var(--muted);
  }
  .card__divider {
    position: absolute;
    left: 240px; top: 110px;
    width: 1.5px; height: 46px;
    background: var(--divider);
  }
  .contact-list {
    position: absolute;
    left: 254px; top: 108px;
    list-style: none;
    font-family: "Arimo", sans-serif;
    font-size: 11.5px;
    color: var(--ink);
  }
  .contact-list li {
    display: flex; align-items: center; gap: 7px;
    height: 16px;
  }
  .contact-list svg { width: 9px; height: 9px; fill: var(--name-blue); flex: none; }
  .card__location {
    position: absolute;
    left: 40px; bottom: 32px;
    font-family: "Arimo", sans-serif;
    font-size: 12px;
    color: var(--ink);
  }
</style>
</head>
<body>

<section class="card card--front">
  <div class="card__tree-decor" role="img" aria-label="Faint large tree decoration"></div>
  <div class="brand">
    <span class="brand__mark"></span>
    <p class="brand__name">Brightpath Horizon</p>
  </div>
  <p class="card__website">www.yourwebsite.com</p>
</section>

<section class="card card--back">
  <div class="identity">
    <p class="identity__name">Daniel Harper</p>
    <p class="identity__role">Founder</p>
  </div>
  <span class="card__divider"></span>
  <ul class="contact-list">
    <li>
      <svg viewBox="0 0 10 10" aria-hidden="true"><path d="M2 0.5 L3.6 0.5 L4.2 3 L3 3.8 Q4 6 6.2 7 L7 5.8 L9.5 6.4 L9.5 8 Q9.5 9.5 8 9.5 Q0.5 9 0.5 2 Q0.5 0.5 2 0.5Z"/></svg>
      555-014-2280
    </li>
    <li>
      <svg viewBox="0 0 10 10" aria-hidden="true"><path d="M0.5 2 H9.5 V8.5 H0.5Z M1.3 2.8 L5 5.6 L8.7 2.8" fill="none" stroke="#2aa5df" stroke-width="1.1"/></svg>
      hello@brightpathmail.com
    </li>
    <li>
      <svg viewBox="0 0 10 10" aria-hidden="true"><circle cx="5" cy="5" r="4.4" fill="none" stroke="#2aa5df" stroke-width="1.1"/><path d="M0.6 5 H9.4 M5 0.6 Q2.2 5 5 9.4 M5 0.6 Q7.8 5 5 9.4" fill="none" stroke="#2aa5df" stroke-width="0.8"/></svg>
      www.BrightpathHorizon.com
    </li>
  </ul>
  <p class="card__location">Location: 480 Harbor View Ln. Seabrook Bay, FL 32011</p>
</section>

</body>
</html>
```